qoBureau Business Card Design Project

We need a business card design for qoBureau. qoBureau is an underwriting agency. Underwriting agencies act on behalf of insurers, to underwrite insurance. We will be operating in specialised classes of insurance initially and looking to expand from there. We would like to see designs that incorporate our logo colours as well as a contrasting stand out colour - also we'd like the logo itself to be embossed on the card.

Industry/Entity Type

Insurance

Requirements
Must have
• Logo on front
Nice to have
• Logo solely featured on back of card
Should not have
• Please do not use comic cans font :)

```html
<!DOCTYPE html>
<html lang="en">
<head>
<meta charset="utf-8">
<title>qoBureau Business Card</title>
<link rel="stylesheet" href="https://fonts.googleapis.com/css2?family=Lato:wght@400;700;900&family=Libre+Baskerville:wght@700&display=swap">
<style>
  :root {
    --page: #ffffff;
    --card-blue-light: #4d8ad6;
    --card-blue: #3a78c9;
    --card-blue-deep: #2a63b4;
    --band-blue: #1f5fc4;
    --ink: #0d1a2e;
    --name-white: #ffffff;
    --brand-light: #e6f0fc;
    --front-brand: rgba(255, 255, 255, 0.6);
    --mark-tone: rgba(255, 255, 255, 0.22);
    --mark-faint: rgba(255, 255, 255, 0.12);
  }
  * { margin: 0; padding: 0; box-sizing: border-box; }
  html, body {
    width: 1200px;
    height: 801px;
    overflow: hidden;
    background: var(--page);
  }
  .canvas {
    position: relative;
    width: 1200px;
    height: 801px;
  }
  .card {
    position: absolute;
    border-radius: 30px;
    overflow: hidden;
  }

  /* Front: contact details */
  .card--contact {
    left: 56px;
    top: 44px;
    width: 618px;
    height: 353px;
    background: linear-gradient(180deg, var(--card-blue-light) 0%, var(--card-blue) 55%, var(--card-blue-deep) 100%);
  }
  .card__texture {
    position: absolute;
    inset: 0;
    background: linear-gradient(180deg, rgba(255,255,255,0.05), rgba(0,0,0,0.07));
  }
  .contact__mark {
    position: absolute;
    left: 185px;
    top: 9px;
    width: 248px;
    height: 248px;
  }
  .contact {
    position: absolute;
    left: 0;
    right: 0;
    top: 78px;
    text-align: center;
    font-family: "Lato", sans-serif;
    color: var(--ink);
  }
  .contact__name {
    font-family: "Libre Baskerville", serif;
    font-weight: 700;
    font-size: 29px;
    line-height: 36px;
    color: var(--name-white);
  }
  .contact__title {
    font-size: 19px;
    font-weight: 700;
    line-height: 22px;
    margin-bottom: 24px;
  }
  .contact__line {
    font-size: 19.5px;
    line-height: 24px;
  }
  .contact__brand {
    position: absolute;
    left: 0;
    right: 0;
    bottom: 16px;
    text-align: center;
    font-family: "Lato", sans-serif;
    font-weight: 900;
    font-size: 22px;
    line-height: 26px;
    color: var(--front-brand);
  }

  /* Back: brand side */
  .card--brand {
    left: 522px;
    top: 410px;
    width: 616px;
    height: 341px;
    background: radial-gradient(ellipse at 50% 40%, var(--card-blue-light) 0%, var(--card-blue) 60%, var(--card-blue-deep) 100%);
  }
  .brand__mark {
    position: absolute;
    left: 243px;
    top: 38px;
    width: 156px;
    height: 156px;
  }
  .brand__name {
    position: absolute;
    left: 0;
    right: 0;
    top: 196px;
    text-align: center;
    font-family: "Lato", sans-serif;
    font-weight: 900;
    font-size: 96px;
    line-height: 110px;
    letter-spacing: -1px;
    color: var(--brand-light);
  }
  .brand__band {
    position: absolute;
    left: 0;
    right: 0;
    bottom: 0;
    height: 44px;
    background: var(--band-blue);
  }
</style>
</head>
<body>
<main class="canvas">
  <section class="card card--contact">
    <div class="card__texture" role="img" aria-label="Faint repeated brand-name texture across the card"></div>
    <svg class="contact__mark" viewBox="0 0 248 248" aria-hidden="true">
      <circle cx="124" cy="124" r="122" fill="var(--mark-faint)"/>
    </svg>
    <div class="contact">
      <p class="contact__name">Your Name</p>
      <p class="contact__title">Job Title</p>
      <p class="contact__line">Company Name</p>
      <p class="contact__line">yourname@yourcompany.com</p>
      <p class="contact__line">232 address Lane1,</p>
      <p class="contact__line">Mobile Number</p>
      <p class="contact__line">Website Address</p>
    </div>
    <p class="contact__brand">qoBureau</p>
  </section>

  <section class="card card--brand">
    <svg class="brand__mark" viewBox="0 0 156 156" aria-hidden="true">
      <circle cx="78" cy="78" r="76" fill="var(--mark-tone)"/>
    </svg>
    <p class="brand__name">qoBureau</p>
    <div class="brand__band"></div>
  </section>
</main>
</body>
</html>
```